Bright and beautiful business card for a coach

I'm a personal and business coach based in Perth, Australia. I need a business card that whilst subtle and elegant, will stand out and appeal on a table full of cards.

My business name is Fern Mentoring and the business card must represent the warmth and brightness implied in the name, without being gimmicky. It must have a warmth and appeal and be easy to read.

I prefer clean, minimalist designs.

It must align with the feel of my website and socials: https://www.fernmentoring-example.com.au/
https://www.instagram.com/fernmentoringau/
https://www.facebook.com/fernmentoringau
Updates

Hi Designers Thank you so much for taking the time to submit designs. I wonder if I could have explained myself a little better. Most of the designs that have been submitted look rather formal and many have quite corporate looking embellishments on them (to my eye). I would like softer, warmer, more organic. I’m open to people playing about and being more abstract, using softer embellishments (e.g the line drawing flowers and grasses I’ve used in my socials) incorporating other colours from my palette or like the social icons in my email signature (in PDF), perhaps playing with size/oversize, playing with the bleed. Please don’t be constrained by what I’ve already done, it merely needs to compliment. I’m sorry if I’m not using the right words or have led you astray. I’m no designer, but I’ve done my website, socials, email signature etc all myself (my logo was a design contest) and I was really hoping for my business card to be something more creative than I could have made with a template. Reminder: No black cards/sides please. Thank you 😊

Target Market(s)

Individuals, most likely but not all female. Creative thinkers. Likely professionals.

Industry/Entity Type

Business & Personal Coach

Contact Information for Business Card

(Fern Mentoring Logo) Name: Greta Pellham; Title: Business & Personal Coach; Phone number: +61 (0)458 913307; Email: greta@fernmentoring-example.com.au; Website: https://fernmentoring-example.com.au; Social icons for Facebook, Instagram & LinkedIn: @fernmentoringAU. Optional strapline: "A steady guide to help you find clarity and calm"

Font styles to use
Sans Serif

Colors
00AB8E
00BBA5
67D7C9
C6EFE9
E9F9F6
59FF00
82FF00
B8FF75
E3FFCB
F4FFEA
FFC000
F8CF3A
FAE287
FDF2CF
FEFAEE

Requirements
Must have
• Must align with feel of my website and socials. Must have a pop of #FFC000 (possibly whole of one side, or at least a block). Bright or white background. Easy to read.
Nice to have
• Possibly incorporate the sunshine/grass picture I have used in website and socials - will upload.
Should not have
• Must not be black or dark. Not impersonal or corporate looking.

```html
<!DOCTYPE html>
<html lang="en">
<head>
<meta charset="utf-8">
<title>Fern Mentoring – Business Card</title>
<link rel="stylesheet" href="https://fonts.googleapis.com/css2?family=Montserrat:wght@400;500;700&display=swap">
<style>
  :root {
    --bg: #c9c9c9;
    --card-white: #ffffff;
    --orange-deep: #b5602a;
    --orange-mid: #d4862a;
    --gold: #f3b81f;
    --text-dark: #4a4a4a;
    --grey-sliver: #a9a9a9;
    --white: #ffffff;
  }
  * { margin: 0; padding: 0; box-sizing: border-box; }
  html, body {
    width: 1200px; height: 788px; overflow: hidden;
    background: var(--bg);
    font-family: "Montserrat", Arial, sans-serif;
  }
  .canvas {
    position: relative; width: 1200px; height: 788px;
    display: flex; align-items: center; justify-content: center; gap: 40px;
  }
  .card {
    position: relative; width: 540px; height: 310px;
    border-radius: 22px; overflow: hidden;
    box-shadow: 0 10px 24px rgba(0,0,0,0.22);
  }
  /* Front */
  .card-front { background: var(--card-white); }
  .card-front .wave { position: absolute; inset: 0; }
  .brand-front {
    position: absolute; left: 24px; top: 118px; width: 176px;
    text-align: center; color: var(--orange-mid);
    font-weight: 500; font-size: 22px; letter-spacing: 1px; line-height: 1.25;
  }
  .divider {
    position: absolute; left: 208px; top: 62px; width: 1px; height: 130px;
    background: var(--gold);
  }
  .contact { position: absolute; left: 224px; top: 40px; color: var(--text-dark); }
  .contact-name {
    font-weight: 700; font-size: 23px; color: var(--orange-deep);
    letter-spacing: 0.5px; text-transform: uppercase; line-height: 1.2;
  }
  .contact-title { font-size: 12.5px; margin-bottom: 8px; }
  .contact-row {
    display: flex; align-items: center; gap: 6px;
    font-size: 11.5px; line-height: 1.65;
  }
  .contact-icon { width: 12px; height: 12px; flex: none; }
  .social-dots { display: flex; gap: 3px; }
  .social-dot {
    width: 12px; height: 12px; border-radius: 50%; background: var(--orange-mid);
  }
  .strapline {
    position: absolute; right: 22px; bottom: 20px;
    color: var(--white); font-size: 11.5px; font-weight: 500;
    line-height: 1.4; text-align: right;
  }
  /* Back */
  .card-back {
    background: linear-gradient(200deg, var(--gold) 0%, var(--orange-mid) 45%, var(--orange-deep) 100%);
    display: flex; align-items: center; justify-content: center;
  }
  .brand-back {
    color: var(--white); font-weight: 500; font-size: 40px; letter-spacing: 2px;
  }
</style>
</head>
<body>
<main class="canvas">
  <section class="card card-front">
    <svg class="wave" viewBox="0 0 540 310" preserveAspectRatio="none" aria-hidden="true">
      <defs>
        <linearGradient id="bandFill" x1="0" y1="1" x2="1" y2="0">
          <stop offset="0" stop-color="#f3b81f"/>
          <stop offset="0.45" stop-color="#d4862a"/>
          <stop offset="1" stop-color="#b5602a"/>
        </linearGradient>
      </defs>
      <path d="M0,300 C180,290 320,250 420,190 S525,110 540,96 L540,310 L0,310 Z" fill="#a9a9a9"/>
      <path d="M0,310 C200,300 340,262 430,200 S530,118 540,104 L540,310 Z" fill="url(#bandFill)"/>
    </svg>

    <div class="brand-front">Fern Mentoring</div>
    <div class="divider"></div>

    <div class="contact">
      <div class="contact-name">Greta Pellham</div>
      <div class="contact-title">Business &amp; Personal Coach</div>
      <div class="contact-row">
        <svg class="contact-icon" viewBox="0 0 12 12"><path d="M3 1 L5 3.5 L4 5 Q5.5 7 7 8 L8.5 7 L11 9 L10 11 Q4 11 1 2 Z" fill="#d4862a"/></svg>
        +61 (0)458 913307
      </div>
      <div class="contact-row">
        <svg class="contact-icon" viewBox="0 0 12 12"><rect x="1" y="2.5" width="10" height="7" fill="#d4862a"/><path d="M1 2.5 L6 6.5 L11 2.5" stroke="#fff" stroke-width="1" fill="none"/></svg>
        greta@fernmentoring-example.com.au
      </div>
      <div class="contact-row">
        <svg class="contact-icon" viewBox="0 0 12 12"><circle cx="6" cy="6" r="5" fill="#d4862a"/><path d="M1 6 H11 M6 1 Q3 6 6 11 M6 1 Q9 6 6 11" stroke="#fff" stroke-width="0.8" fill="none"/></svg>
        fernmentoring-example.com.au
      </div>
      <div class="contact-row">
        <span class="social-dots"><span class="social-dot"></span><span class="social-dot"></span><span class="social-dot"></span></span>
        @fernmentoringAU
      </div>
    </div>

    <p class="strapline">A steady guide to help you<br>find clarity and calm</p>
  </section>

  <section class="card card-back">
    <div class="brand-back">Fern Mentoring</div>
  </section>
</main>
</body>
</html>
```